Redesign of business card for Cedar Ridge Mechanical

We are looking for a new design for our business cards for Cedar Ridge Mechanical. We are a plumbing & HVAC construction company, operating on the West Coast of Canada and USA. Logo attached.
Industry/Entity Type
Construction - Plumbing & HVAC
Contact Information for Business Card
Name, address, phone numbers, email, website address
Look and feel
Each slider illustrates characteristics of the customer's brand and the style your logo design should communicate.

```html
<!DOCTYPE html>
<html lang="en">
<head>
<meta charset="utf-8">
<title>Cedar Ridge Mechanical — Business Card</title>
<link rel="stylesheet" href="https://fonts.googleapis.com/css2?family=Poppins:wght@300;400;600&display=swap">
<style>
  :root {
    --bg: #d6d6d6;
    --paper: #efeee8;
    --ink: #111111;
    --rule: #2a2a2a;
  }
  * { box-sizing: border-box; margin: 0; padding: 0; }
  html, body { width: 1200px; height: 711px; overflow: hidden; }
  body {
    background: var(--bg);
    font-family: "Poppins", sans-serif;
    color: var(--ink);
    position: relative;
  }
  .card {
    position: absolute;
    top: 200px;
    width: 540px;
    height: 309px;
    background: var(--paper);
    box-shadow: 0 10px 28px rgba(0,0,0,0.22);
    overflow: hidden;
  }
  .card--details { left: 40px; }
  .card--brand { left: 620px; }

  .edge-bar { position: absolute; width: 9px; background: var(--ink); }
  .edge-bar--left { left: 0; top: 28px; height: 130px; }
  .edge-bar--right { right: 0; bottom: 24px; height: 150px; }

  .wordmark {
    display: flex;
    align-items: center;
    gap: 12px;
    font-weight: 600;
    text-transform: uppercase;
    line-height: 1.1;
  }
  .wordmark__square { background: var(--ink); flex: none; }

  /* brand side */
  .card--brand .wordmark {
    position: absolute;
    left: 50%; top: 50%;
    transform: translate(-50%, -50%);
    font-size: 30px;
    letter-spacing: 1px;
  }
  .card--brand .wordmark__square { width: 40px; height: 40px; }

  /* details side */
  .card--details .wordmark {
    position: absolute;
    left: 40px; top: 92px;
    width: 210px;
    font-size: 19px;
  }
  .card--details .wordmark__square { width: 24px; height: 24px; }

  .address {
    position: absolute;
    left: 40px; top: 205px;
    width: 210px;
    font-size: 11.5px;
    line-height: 1.55;
  }
  .divider {
    position: absolute;
    left: 268px; top: 70px;
    width: 1px; height: 170px;
    background: var(--rule);
  }
  .person { position: absolute; left: 292px; top: 82px; }
  .person__name { font-size: 24px; line-height: 1.1; font-weight: 300; }
  .person__name strong { font-weight: 600; }
  .person__title { font-size: 12px; margin-top: 2px; }

  .contact-list { list-style: none; margin-top: 20px; font-size: 12px; }
  .contact-list li { display: flex; align-items: center; gap: 8px; margin-bottom: 5px; }
  .contact-list svg { width: 12px; height: 12px; flex: none; }
</style>
</head>
<body>

<section class="card card--details" aria-label="Business card, contact side">
  <span class="edge-bar edge-bar--left"></span>
  <span class="edge-bar edge-bar--right"></span>

  <div class="wordmark">
    <span class="wordmark__square"></span>
    <span>Cedar Ridge Mechanical</span>
  </div>
  <p class="address">1840 Harbor Way Suite 310<br>Vancouver, BC V6B 2K9</p>

  <span class="divider"></span>

  <div class="person">
    <h1 class="person__name"><strong>Marta</strong> Kovalenko</h1>
    <p class="person__title">Founder &amp; CEO</p>
    <ul class="contact-list">
      <li>
        <svg viewBox="0 0 24 24" aria-hidden="true"><path fill="currentColor" d="M6.6 10.8a15.1 15.1 0 0 0 6.6 6.6l2.2-2.2a1 1 0 0 1 1-.25 11.4 11.4 0 0 0 3.6.57 1 1 0 0 1 1 1V20a1 1 0 0 1-1 1A17 17 0 0 1 3 4a1 1 0 0 1 1-1h3.5a1 1 0 0 1 1 1c0 1.25.2 2.45.57 3.6a1 1 0 0 1-.25 1z"/></svg>
        (604) 555-0148
      </li>
      <li>
        <svg viewBox="0 0 24 24" aria-hidden="true"><circle cx="12" cy="12" r="9" fill="none" stroke="currentColor" stroke-width="2"/><path d="M3 12h18M12 3c3 3 3 15 0 18M12 3c-3 3-3 15 0 18" fill="none" stroke="currentColor" stroke-width="1.6"/></svg>
        info@cedarridgemech.com
      </li>
      <li>
        <svg viewBox="0 0 24 24" aria-hidden="true"><rect x="2" y="5" width="20" height="14" fill="none" stroke="currentColor" stroke-width="2"/><path d="M2 5l10 8 10-8" fill="none" stroke="currentColor" stroke-width="2"/></svg>
        www.cedarridgemech.com
      </li>
    </ul>
  </div>
</section>

<section class="card card--brand" aria-label="Business card, brand side">
  <span class="edge-bar edge-bar--left"></span>
  <span class="edge-bar edge-bar--right"></span>
  <div class="wordmark">
    <span class="wordmark__square"></span>
    <span>Cedar Ridge Mechanical</span>
  </div>
</section>

</body>
</html>
```